New website for concierge mobile medical service

new website for business:
WEBSITE REQUEST LIST:
Luxury product look.
Professional. Clean & simple, NO stock people photos. Graphics OK.
Black and white text.

```html
<!DOCTYPE html>
<html lang="en">
<head>
<meta charset="utf-8">
<title>Lumen Care – Optimal Wellness</title>
<link href="https://fonts.googleapis.com/css2?family=Lato:wght@400;700;900&display=swap" rel="stylesheet">
<style>
:root{
  --ink:#1e1e1e;
  --body:#333;
  --blue:#1a7fb5;
  --purple:#7a6bb5;
  --navy:#062338;
  --teal:#178fae;
  --pale-teal:#9bd8e0;
  --line:#dcdcdc;
  --footer:#2b2b2b;
  --white:#fff;
}
*{box-sizing:border-box;margin:0;padding:0}
html,body{width:885px;height:1200px;overflow:hidden;background:var(--white);font-family:'Lato',sans-serif;color:var(--body)}
.page{position:relative;width:885px;height:1200px}
.abs{position:absolute}

/* header */
.site-header{position:absolute;left:0;top:0;width:885px;height:79px;background:var(--white);z-index:2}
.brand{position:absolute;left:115px;top:14px;width:90px;height:90px;border-radius:50%;background:var(--navy);border:6px solid var(--white);box-shadow:0 0 0 3px #8fd0e0;display:flex;align-items:center;justify-content:center;color:var(--white);font-size:14px;font-weight:700;text-align:center;line-height:1.1}
.phone{position:absolute;right:105px;top:12px;display:flex;align-items:center;gap:9px;color:var(--purple);font-weight:700;font-size:14px}
.phone-icon{width:24px;height:24px;background:var(--purple);border-radius:2px;display:flex;align-items:center;justify-content:center}
.main-nav a{position:absolute;top:56px;font-size:9.5px;font-weight:700;color:var(--ink);text-decoration:none;letter-spacing:.1px}
.main-nav a.active{color:#0f5d7a}
.nav-underline{position:absolute;left:657px;top:75px;width:49px;height:4px;background:#0f5d7a}

/* hero */
.hero{position:absolute;left:0;top:79px;width:885px;height:195px;background:linear-gradient(100deg,#000a12 0%,#03213a 45%,#0b4a74 100%)}
.hero h1{position:absolute;left:106px;top:75px;font-size:33px;font-weight:900;color:var(--white)}
.hero-emblem{position:absolute;left:638px;top:21px;width:152px;height:152px;border-radius:50%;border:3px solid #7fd9ee;background:radial-gradient(circle,#1a4f78 0%,#0c3a5e 70%)}

/* content */
.content h2{position:absolute;left:107px;top:307px;font-size:16.5px;font-weight:700;color:var(--blue)}
.content p.lead{position:absolute;left:107px;top:334px;width:660px;font-size:10.2px;line-height:19px}
.content h3{position:absolute;left:107px;top:399px;font-size:13px;font-weight:700;color:var(--purple)}
.content p.intro{position:absolute;left:107px;top:425px;font-size:10.2px}
.goal-list{list-style:none;position:absolute;top:448px}
.goal-list li{height:23.5px;display:flex;align-items:center;gap:12px;font-size:10.4px;color:#2a2a2a}
.goal-list svg{flex:none}

/* subscribe */
.subscribe{position:absolute;left:0;top:595px;width:885px;height:186px;background:linear-gradient(110deg,#1a9ab5 0%,#2185a3 50%,#1397b3 100%)}
.subscribe h2{position:absolute;width:100%;top:32px;text-align:center;font-size:24px;font-weight:700;color:var(--white)}
.field{position:absolute;background:var(--white);font-size:9.5px;color:#333;padding-left:11px;display:flex;align-items:center}
.field.bordered{border:1px solid var(--line)}
.btn{position:absolute;background:var(--pale-teal);color:var(--white);font-size:12px;font-weight:700;display:flex;align-items:center;justify-content:center;letter-spacing:.2px}

/* contact */
.contact h2{position:absolute;width:100%;top:796px;text-align:center;font-size:24px;font-weight:700;color:var(--ink)}
.contact p{position:absolute;width:100%;top:848px;text-align:center;font-size:12px;color:var(--ink)}

/* footer */
.site-footer{position:absolute;left:0;top:1100px;width:885px;height:100px;background:var(--footer);color:var(--white)}
.footer-nav{position:absolute;top:17px;width:100%;display:flex;justify-content:center;gap:29px;font-size:9.5px;font-weight:700}
.copyright{position:absolute;top:43px;width:100%;text-align:center;font-size:8.3px}
.social{position:absolute;top:62px;width:100%;display:flex;justify-content:center;gap:13px}
.social span{width:12px;height:12px;border-radius:50%;background:var(--white)}
</style>
</head>
<body>
<div class="page">

  <header class="site-header">
    <div class="brand">Lumen<br>Care</div>
    <div class="phone">
      <span class="phone-icon">
        <svg width="12" height="12" viewBox="0 0 24 24"><path fill="#fff" d="M6.6 10.8a15.1 15.1 0 0 0 6.6 6.6l2.2-2.2c.3-.3.7-.4 1-.2 1.1.4 2.3.6 3.6.6.6 0 1 .4 1 1V20c0 .6-.4 1-1 1A17 17 0 0 1 3 4c0-.6.4-1 1-1h3.5c.6 0 1 .4 1 1 0 1.3.2 2.5.6 3.6.1.3 0 .7-.2 1z"/></svg>
      </span>
      555-010-0199
    </div>
    <nav class="main-nav">
      <a style="left:291px">HOME</a>
      <a style="left:349px">ABOUT US</a>
      <a style="left:427px">WHY LUMEN?</a>
      <a style="left:513px">SERVICE AREA</a>
      <a style="left:609px">OTHER</a>
      <a class="active" style="left:671px">FAQ</a>
      <a style="left:719px">CONTACT US</a>
    </nav>
    <div class="nav-underline"></div>
  </header>

  <section class="hero">
    <h1>Optimal Wellness</h1>
    <div class="hero-emblem" role="img" aria-label="Emblem of a car with a medical caduceus above it"></div>
  </section>

  <section class="content">
    <h2>Why does Lumen Care include optimal wellness as part of my care</h2>
    <p class="lead">As physicians, we believe customized wellness care will give you the plan and tools needed to improve your overall health and vitality. We will help you manage important aspects of your health that contribute to an improved healthspan including longevity and feeling better every day.</p>
    <h3>What does wellness care look like?</h3>
    <p class="intro">We will help you set and achieve goals such as:</p>
    <ul class="goal-list" style="left:107px">
      <li><svg width="10" height="10" viewBox="0 0 20 20"><circle cx="10" cy="10" r="10" fill="#1a8fd0"/><path d="M5.5 10.2l3 3 6-6" stroke="#fff" stroke-width="2.4" fill="none"/></svg>Weight management</li>
      <li><svg width="10" height="10" viewBox="0 0 20 20"><circle cx="10" cy="10" r="10" fill="#1a8fd0"/><path d="M5.5 10.2l3 3 6-6" stroke="#fff" stroke-width="2.4" fill="none"/></svg>Fat loss</li>
      <li><svg width="10" height="10" viewBox="0 0 20 20"><circle cx="10" cy="10" r="10" fill="#1a8fd0"/><path d="M5.5 10.2l3 3 6-6" stroke="#fff" stroke-width="2.4" fill="none"/></svg>Nutritional health</li>
      <li><svg width="10" height="10" viewBox="0 0 20 20"><circle cx="10" cy="10" r="10" fill="#1a8fd0"/><path d="M5.5 10.2l3 3 6-6" stroke="#fff" stroke-width="2.4" fill="none"/></svg>Age-optimal fitness</li>
      <li><svg width="10" height="10" viewBox="0 0 20 20"><circle cx="10" cy="10" r="10" fill="#1a8fd0"/><path d="M5.5 10.2l3 3 6-6" stroke="#fff" stroke-width="2.4" fill="none"/></svg>Hormonal balance</li>
    </ul>
    <ul class="goal-list" style="left:277px">
      <li><svg width="10" height="10" viewBox="0 0 20 20"><circle cx="10" cy="10" r="10" fill="#1a8fd0"/><path d="M5.5 10.2l3 3 6-6" stroke="#fff" stroke-width="2.4" fill="none"/></svg>Customized supplements / vitamins</li>
      <li><svg width="10" height="10" viewBox="0 0 20 20"><circle cx="10" cy="10" r="10" fill="#1a8fd0"/><path d="M5.5 10.2l3 3 6-6" stroke="#fff" stroke-width="2.4" fill="none"/></svg>Stress management</li>
      <li><svg width="10" height="10" viewBox="0 0 20 20"><circle cx="10" cy="10" r="10" fill="#1a8fd0"/><path d="M5.5 10.2l3 3 6-6" stroke="#fff" stroke-width="2.4" fill="none"/></svg>Sleep hygiene</li>
      <li><svg width="10" height="10" viewBox="0 0 20 20"><circle cx="10" cy="10" r="10" fill="#1a8fd0"/><path d="M5.5 10.2l3 3 6-6" stroke="#fff" stroke-width="2.4" fill="none"/></svg>Smoking cessation</li>
    </ul>
  </section>

  <section class="subscribe" role="img" aria-label="Teal medical themed background">
    <h2>Subscribe</h2>
    <div class="field" style="left:204px;top:76px;width:234px;height:33px">Enter Name</div>
    <div class="field" style="left:447px;top:76px;width:234px;height:33px">Enter Email Address</div>
    <div class="btn" style="left:204px;top:115px;width:477px;height:33px">SUBSCRIBE NOW</div>
  </section>

  <section class="contact">
    <h2>Contact Us</h2>
    <p>We want to hear from you! Click below to send us a message and receive upcoming information.</p>
    <div class="field bordered" style="left:165px;top:877px;width:269px;height:30px">Enter Name</div>
    <div class="field bordered" style="left:452px;top:877px;width:270px;height:30px;padding-left:13px">Enter Email Address</div>
    <div class="field bordered" style="left:165px;top:916px;width:269px;height:30px">Phone No</div>
    <div class="field bordered" style="left:452px;top:916px;width:270px;height:30px;padding-left:13px">Subject</div>
    <div class="field bordered" style="left:165px;top:953px;width:557px;height:74px;align-items:flex-start;padding-top:13px">Message</div>
    <div class="btn" style="left:204px;top:1040px;width:478px;height:33px">SUBMIT NOW</div>
  </section>

  <footer class="site-footer">
    <nav class="footer-nav">
      <span>HOME</span><span>ABOUT US</span><span>WHY LUMEN?</span><span>SERVICE AREA</span><span>OTHER</span><span>CONTACT US</span>
    </nav>
    <div class="copyright">Copyright © 2019.&nbsp; Company Name&nbsp; All Rights Reserved</div>
    <div class="social" aria-label="Social media links">
      <span></span><span></span><span></span><span></span><span></span>
    </div>
  </footer>

</div>
</body>
</html>
```